RWT Fittings Ltd Business Cards

We need a business card with our business logo. We provide window and door installations on high-rises in west coast British Colombia, Canada.

I would like my business information and details on one side of the card, and the other side the company name with logo

Target Market(s)

General Contractors

Industry/Entity Type

Construction

Contact Information for Business Card

one side i want my company name and logo in the dark theme logo that i provided

Requirements
Must have
• Marco Peltieri, 16045518293, RWTFittings@mailbox-demo.com, 1407-5194 Linden Row Burnaby BC, V5H 2K9, Owner & Manager

```html
<!DOCTYPE html>
<html lang="en">
<head>
<meta charset="utf-8">
<title>RWT Fittings Ltd – Business Cards</title>
<link rel="stylesheet" href="https://fonts.googleapis.com/css2?family=Roboto:wght@400;700&display=swap">
<style>
  :root {
    --backdrop: #232323;
    --card: #202125;
    --card-shade: #2a2c31;
    --blue: #29a8e0;
    --grey-text: #b9babc;
    --white-text: #e9e9e9;
    --emboss: #17181b;
  }
  * { margin: 0; padding: 0; box-sizing: border-box; }
  html, body { width: 1200px; height: 780px; overflow: hidden; background: var(--backdrop); }
  body { font-family: "Roboto", Arial, sans-serif; position: relative; }

  .card {
    position: absolute;
    top: 235px;
    width: 530px;
    height: 310px;
    background: var(--card);
    border-radius: 4px;
    overflow: hidden;
    box-shadow: 0 18px 40px rgba(0,0,0,.45);
  }
  .card--front { left: 40px; }
  .card--back { left: 630px; }

  .wordmark {
    display: flex;
    align-items: center;
    gap: 10px;
    font-weight: 700;
    letter-spacing: 1.5px;
    text-transform: uppercase;
  }
  .wordmark__square { display: block; flex: none; }

  .card--front .wordmark {
    position: absolute;
    left: 34px;
    top: 34px;
    color: var(--blue);
    font-size: 26px;
  }
  .card--front .wordmark__square { width: 30px; height: 30px; background: var(--blue); }

  .decor-block {
    position: absolute;
    right: -40px;
    bottom: -50px;
    width: 300px;
    height: 300px;
    background: var(--card-shade);
    opacity: .75;
  }

  .contact {
    position: absolute;
    left: 34px;
    top: 110px;
    list-style: none;
    color: var(--white-text);
    font-size: 13.5px;
    line-height: 1.5;
  }
  .contact__address { margin-bottom: 8px; }
  .contact__row { display: flex; align-items: center; gap: 8px; }
  .contact__icon { width: 13px; height: 13px; flex: none; }

  .person {
    position: absolute;
    right: 40px;
    bottom: 58px;
    text-align: left;
  }
  .person__name { font-size: 30px; font-weight: 700; line-height: 1.1; }
  .person__first { color: var(--blue); }
  .person__last { color: var(--grey-text); }
  .person__role { color: var(--white-text); font-size: 15px; margin-top: 4px; }

  .accent-bar {
    position: absolute;
    right: 0;
    bottom: 22px;
    width: 24px;
    height: 56px;
    background: var(--blue);
  }

  .card--back .wordmark {
    position: absolute;
    left: 50%;
    top: 50%;
    transform: translate(-50%, -50%);
    color: var(--emboss);
    font-size: 34px;
    white-space: nowrap;
    text-shadow: none;
  }
  .card--back .wordmark__square { width: 38px; height: 38px; background: var(--emboss); }
</style>
</head>
<body>

  <section class="card card--front" aria-label="Business card, contact side">
    <div class="decor-block"></div>

    <div class="wordmark">
      <span class="wordmark__square"></span>
      <span class="wordmark__name">RWT Fittings Ltd</span>
    </div>

    <ul class="contact">
      <li class="contact__address">1407-5194 Linden Row<br>Burnaby BC, V5H 2K9</li>
      <li class="contact__row">
        <svg class="contact__icon" viewBox="0 0 24 24" aria-hidden="true">
          <path fill="#29a8e0" d="M6.6 10.8a15.1 15.1 0 0 0 6.6 6.6l2.2-2.2c.3-.3.7-.4 1-.2 1.1.4 2.3.6 3.6.6.6 0 1 .4 1 1V20c0 .6-.4 1-1 1A17 17 0 0 1 3 4c0-.6.4-1 1-1h3.5c.6 0 1 .4 1 1 0 1.3.2 2.5.6 3.6.1.3 0 .7-.2 1z"/>
        </svg>
        <span>1604 551 8293</span>
      </li>
      <li class="contact__row">
        <svg class="contact__icon" viewBox="0 0 24 24" aria-hidden="true">
          <rect x="2" y="5" width="20" height="14" rx="2" fill="#29a8e0"/>
          <path d="M3 6l9 7 9-7" fill="none" stroke="#202125" stroke-width="2"/>
        </svg>
        <span>RWTFittings@mailbox-demo.com</span>
      </li>
    </ul>

    <div class="person">
      <p class="person__name"><span class="person__first">Marco</span> <span class="person__last">Peltieri</span></p>
      <p class="person__role">Owner &amp; Manager</p>
    </div>

    <div class="accent-bar"></div>
  </section>

  <section class="card card--back" aria-label="Business card, company side">
    <div class="wordmark">
      <span class="wordmark__square"></span>
      <span class="wordmark__name">RWT Fittings Ltd</span>
    </div>
  </section>

</body>
</html>
```